Terravista NQ PPT template - non-profit company - minerals, energy, water, geothermal resources

Terravista NQ requires two (Letter-sized and 16:9)simple, flexible and clean PowerPoint templates that can be used for corporate and research project presentations and meeting materials

Each layout should have correct colours, fonts and size as a default (focus area colours for headings; secondary colours for body text). Each slide should have the Terravista NQ logo. Slide number should be automatically generated, with no slide number on title slide.

Target Market(s)

Varied, but almost always professional: Government; Community leaders; Mineral/Energy industries; and Academic researchers.

Font styles to use
Serif
Sans Serif
Other font styles liked:
• Calibri, or whatever in style guide

Requirements
Must have
• Two version that we can use – both need to match:
- 16:9 slide size for on-screen presentations; and
- Letter (8.5 x 11 inch) for meeting materials that are printed.

Must use colours in logo as listed in the style guide
Nice to have
• Consistency
Should not have
• Should not be black and white - needs colour

```html
<!DOCTYPE html>
<html lang="en">
<head>
<meta charset="utf-8">
<title>Terravista NQ – Slide Template Overview</title>
<link rel="stylesheet" href="https://fonts.googleapis.com/css2?family=Questrial&family=Source+Sans+3:wght@400;600;700&family=PT+Sans:wght@400;700&display=swap">
<style>
  :root{
    --orange:#e07b39;
    --green:#4fa845;
    --blue:#2a9fc9;
    --slate:#4b5a66;
    --page:#f0f0f0;
    --white:#ffffff;
    --head:"Questrial", sans-serif;
    --body:"Source Sans 3", sans-serif;
  }
  *{margin:0;padding:0;box-sizing:border-box}
  html,body{width:771px;height:1200px;overflow:hidden;background:var(--page)}
  .canvas{position:relative;width:771px;height:1200px;background:var(--page);font-family:var(--body)}
  .slide{position:absolute;width:362px;height:204px;background:var(--white);overflow:hidden;box-shadow:0 1px 4px rgba(0,0,0,.22)}
  .slide::before{content:"";position:absolute;left:0;top:0;right:0;height:3px;z-index:5;
    background:linear-gradient(90deg,var(--orange) 0 28%,var(--green) 28% 65%,var(--blue) 65% 100%)}
  .col-l{left:15px}.col-r{left:395px}
  .row1{top:35px}.row2{top:267px}.row3{top:499px}.row4{top:730px}.row5{top:962px}
  .abs{position:absolute}
  .photo{position:absolute}
  .brand{position:absolute;left:20px;bottom:4px;display:flex;align-items:center;gap:3px;font-family:var(--head);font-size:6.5px;color:var(--slate);font-weight:400}
  .brand i{display:block;width:5px;height:5px;border-radius:50%;background:var(--orange)}
  .pageno{position:absolute;right:12px;bottom:8px;font-size:3.5px;color:var(--slate)}
  .txt{font-size:4.2px;line-height:1.3;text-align:justify}
  .txt p{margin-bottom:2px}
  .o{color:var(--orange)}.g{color:var(--green)}.s{color:var(--slate)}
  .h{font-family:var(--head)}
  ul.list{list-style:none;font-size:4px;line-height:1.9}
  ul.list li::before{content:"•";margin-right:5px}
  .icon-disc{position:absolute;width:50px;height:50px;border-radius:50%;background:var(--white);display:flex;align-items:center;justify-content:center}
  .sub-b{font-weight:700;font-size:4.8px;margin:3px 0 1px}
</style>
</head>
<body>
<div class="canvas">

  <!-- Cover -->
  <section class="slide col-l row1">
    <div class="photo" role="img" aria-label="Satellite geology image of mountain terrain" style="inset:0;background:linear-gradient(135deg,#6f8a6a,#7c6f9c 35%,#5f8f78 60%,#8a7a5a 85%,#647e91)"></div>
    <div class="abs" style="left:0;right:0;top:100px;height:52px;background:rgba(225,225,225,.8)"></div>
    <div class="brand" style="left:45px;top:128px;bottom:auto;font-size:12.5px;gap:5px"><i style="width:9px;height:9px"></i>Terravista NQ</div>
    <div class="abs" style="left:195px;top:104px;font-family:'PT Sans',sans-serif;font-size:22px;color:var(--slate);letter-spacing:-.5px">Monthly Report</div>
    <div class="abs" style="left:252px;top:134px;font-family:'PT Sans',sans-serif;font-size:8px;color:var(--slate)">May 2020</div>
  </section>

  <!-- Chair & CEO message -->
  <section class="slide col-r row1">
    <div class="photo" role="img" aria-label="Two geologists reviewing a geology map" style="left:18px;top:20px;width:91px;height:83px;background:linear-gradient(160deg,#8c8078,#3e6fb3 55%,#d8d2c6)"></div>
    <div class="abs h s" style="left:115px;top:22px;font-size:23px;line-height:.98;font-weight:700;font-family:'PT Sans',sans-serif">CHAIR &amp;<br>CEO<br>MESSAGE</div>
    <div class="abs txt s" style="left:115px;top:106px;width:120px;font-weight:600">
      <p>Our collaborative approach is generating more coordinated, relevant research projects and broadening the awareness of the fundamental value of public geoscience to everyone.</p>
      <p>Sharing results publicly and developing understanding of Terravista NQ's research is stimulating innovation, informing investment and resource development decisions and catalyzing socio-economic opportunities in many regions of the province.</p>
    </div>
    <div class="photo" role="img" aria-label="Helicopter landed on a rocky mountain ridge" style="left:248px;top:0;width:114px;height:204px;background:linear-gradient(170deg,#6fa9d6,#b07a3e 40%,#7a5a3a 75%,#c9c3b8)"></div>
    <div class="brand"><i></i>Terravista NQ</div>
  </section>

  <!-- Minerals section -->
  <section class="slide col-l row2">
    <div class="abs h o" style="left:18px;top:23px;font-size:20px;line-height:.98;font-family:'PT Sans',sans-serif">MI<br>NE<br>RA<br>LS</div>
    <div class="abs o" style="left:74px;top:90px;width:104px">
      <div class="sub-b" style="font-size:4.2px">Identifying New Natural Resource Opportunities</div>
      <div class="txt">We are helping to identify new natural resource opportunities in the province by investing in minerals projects that deliver new earth science and baseline data for prospectors, explorers, mine developers, governments, community leaders and Indigenous groups.</div>
      <div class="sub-b" style="font-size:4.6px;margin-top:4px">Content</div>
      <ul class="list" style="margin-left:1px">
        <li>Identifying New Natural Resource Opportunities</li>
        <li>Major New Regional Projects Announced</li>
        <li>Preserving NQ's Earth Science Legacy</li>
        <li>Tools for Mineral Discovery</li>
      </ul>
    </div>
    <div class="photo" role="img" aria-label="Close-up of layered mineral rock" style="left:207px;top:0;width:155px;height:204px;background:linear-gradient(150deg,#9b8a7c,#c98a5c 35%,#d9d3cc 55%,#4b5766 85%)"></div>
    <div class="icon-disc" style="left:259px;top:77px">
      <svg width="28" height="28" viewBox="0 0 28 28" fill="none" stroke="var(--orange)" stroke-width="1.6" stroke-linecap="round">
        <path d="M4 9 C10 3 18 3 24 9"/><path d="M14 6 L22 24"/>
      </svg>
    </div>
    <div class="brand"><i></i>Terravista NQ</div>
  </section>

  <!-- Major new projects -->
  <section class="slide col-r row2">
    <div class="photo" role="img" aria-label="Satellite geology image of a mountain region" style="left:30px;top:3px;width:332px;height:117px;background:linear-gradient(120deg,#5e8a5a,#7b6fa0 40%,#6b9a7a 70%,#8f8a6a)"></div>
    <div class="abs h o" style="left:33px;top:128px;font-size:13px;line-height:1">Major New Regional<br>Projects Announced</div>
    <div class="abs o" style="left:192px;top:126px;width:155px;font-size:7px;line-height:1.3;text-align:justify">In 2019, we launched two new major minerals projects that are delivering new earth science information to focus the search for mineral deposits, increase discovery rates, encourage investment and promote responsible mineral development in our province.</div>
    <div class="pageno">4</div>
    <div class="brand"><i></i>Terravista NQ</div>
  </section>

  <!-- Tools for mineral discovery -->
  <section class="slide col-l row3">
    <div class="abs h o" style="left:18px;top:45px;font-size:14px;line-height:1.2">Tools for Mineral<br>Discovery</div>
    <div class="abs txt o" style="left:18px;top:83px;width:120px">
      <p>To help find new mineral deposits across the province, we are advancing innovative new mineral exploration tools and methods.</p>
      <p>Field teams combine geochemistry, geophysics and mapping to sharpen targets. Each survey adds to a growing public record that explorers, planners and researchers can use freely. Results are released in open formats, reviewed by partners and updated as new samples come in. This shared base of knowledge helps lower risk for early exploration and supports wise land use decisions across the region for years to come.</p>
    </div>
    <div class="photo" role="img" aria-label="Geologist climbing a striped rock slope" style="left:158px;top:3px;width:68px;height:201px;background:linear-gradient(170deg,#8d8a86,#9a6a52 40%,#6a5a5a 65%,#cfd3d6)"></div>
    <div class="photo" role="img" aria-label="Aerial satellite texture of terrain" style="left:226px;top:3px;width:68px;height:201px;background:linear-gradient(170deg,#6b8a64,#8a82a2 50%,#5d8670)"></div>
    <div class="photo" role="img" aria-label="Close-up of mineral rock surface" style="left:294px;top:3px;width:68px;height:201px;background:linear-gradient(170deg,#a08876,#d4cbc3 45%,#566370 80%)"></div>
    <div class="brand"><i></i>Terravista NQ</div>
  </section>

  <!-- Minerals research -->
  <section class="slide col-r row3">
    <div class="abs h o" style="left:18px;top:20px;font-size:13px;font-family:'PT Sans',sans-serif">MINERALS</div>
    <div class="abs h o" style="left:18px;top:36px;font-size:8.5px;line-height:1.25">Research to Support Future<br>Global Minerals Demand</div>
    <div class="abs txt" style="left:18px;top:59px;width:211px;font-size:3.6px">
      <div class="o">
        <p style="margin:0">The Nordquist Region's competitive advantages include significant deposits of important metals such as copper, gold, molybdenum, silver and zinc as well as steel-making coal and industrial minerals. Global demand for many of these commodities is set to grow to meet the needs of an electrified economy.</p>
        <p style="margin:0">Mineral exploration and mining play a vital role in the regional economy, with large exploration spending and strong gross mining revenue in 2018.</p>
        <p>To compete and thrive in the long term, relevant information and innovative public geoscience research are needed to solve challenges, attract investment and support responsible development. This section highlights new, ongoing and completed research in 2019.</p>
      </div>
      <div class="s sub-b" style="font-size:4.4px">Identifying New Natural Resource Opportunities</div>
      <p class="s">To help identify new opportunities in the province, our goals are to continue regional-scale surveys that deliver large data sets, identify prospective targets, increase discovery rates and add value to existing data through ground-truthing studies.</p>
      <div class="s sub-b" style="font-size:4.4px">Minerals in the Ridgeback Boundary Region</div>
      <p class="s">Field crews sampled stream sediments and bedrock across the region, building a new geochemical dataset. Early results point to several promising trends that will be tested next season with partner groups, local explorers and academic teams working together on shared goals.</p>
    </div>
    <div class="photo" role="img" aria-label="Two field geologists working outdoors near mountains" style="left:242px;top:3px;width:120px;height:201px;background:linear-gradient(160deg,#c9ccce,#8a9a8a 40%,#3b4a5e 65%,#5a5652)"></div>
    <div class="brand"><i></i>Terravista NQ</div>
  </section>

  <!-- More for minerals -->
  <section class="slide col-l row4">
    <div class="abs h o" style="left:18px;top:25px;font-size:24px;line-height:1.25;font-family:'PT Sans',sans-serif">More<br>for<br>Minerals</div>
    <div class="photo" role="img" aria-label="Helicopter on a mountain ridge" style="left:133px;top:3px;width:65px;height:66px;background:linear-gradient(160deg,#6fa0c8,#a8743f 55%,#6a5038)"></div>
    <div class="photo" role="img" aria-label="Geologists working in the field" style="left:133px;top:69px;width:65px;height:66px;background:linear-gradient(160deg,#c8cbcd,#7a8878 45%,#3d4656)"></div>
    <div class="photo" role="img" aria-label="Striped rock outcrop" style="left:133px;top:135px;width:65px;height:69px;background:linear-gradient(160deg,#9a6a52,#8a8580 50%,#d0d3d6)"></div>
    <div class="abs" style="left:208px;top:10px;width:134px">
      <div class="o sub-b">Field Program Update</div>
      <div class="txt s">Crews completed new mapping across the northern ranges this month. Samples are now at the lab and first results are due soon. Data will be released to the public once checked, along with maps and a short summary report for users.<br>Partners joined two site visits and shared useful local knowledge.</div>
      <div class="o sub-b" style="margin-top:10px">New Data Releases</div>
      <div class="txt s">Two new datasets went live this month, covering geochemistry and airborne magnetics. Both are free to download and come with notes on methods, accuracy and suggested uses for explorers and planners.<br>Feedback from users will guide the next round of releases.</div>
      <div class="o sub-b" style="margin-top:10px">Community Outreach</div>
      <div class="txt s">Our team hosted public sessions in three towns to explain current projects and answer questions. Turnout was strong and many visitors asked about water and land use.<br>Further sessions are planned for the autumn across the region.</div>
    </div>
    <div class="pageno" style="right:16px">8</div>
    <div class="brand"><i></i>Terravista NQ</div>
  </section>

  <!-- Oil & gas section -->
  <section class="slide col-r row4">
    <div class="abs h g" style="left:18px;top:20px;font-size:20px;line-height:.98;font-family:'PT Sans',sans-serif">OIL<br>&amp;<br>GAS</div>
    <div class="abs g" style="left:73px;top:90px;width:105px">
      <div class="txt" style="font-size:4.6px">We are collecting, interpreting and sharing new scientific data relating to natural gas development to guide clean, responsible energy development, minimize impacts, answer specific environmental and social questions and attract investment to NQ.</div>
      <div class="sub-b" style="font-size:4.8px;margin-top:4px">Content</div>
      <ul class="list" style="font-size:4.4px;line-height:1.6">
        <li>Facilitating Responsible Natural Resource Development</li>
        <li>Innovation &amp; Technology</li>
        <li>Geothermal</li>
      </ul>
    </div>
    <div class="photo" role="img" aria-label="Geothermal steam rising over a forest" style="left:207px;top:3px;width:155px;height:201px;background:linear-gradient(175deg,#7f8a96,#c9ccd0 45%,#4a5460 70%,#2e3a34)"></div>
    <div class="icon-disc" style="left:259px;top:77px">
      <svg width="30" height="30" viewBox="0 0 30 30" fill="none" stroke="var(--green)" stroke-width="1.3" stroke-linecap="round">
        <path d="M15 8a6 6 0 0 0-3.5 10.9V21h7v-2.1A6 6 0 0 0 15 8z"/><path d="M12 23h6M13 25h4"/>
        <path d="M15 3v2M6 7l1.5 1.5M24 7l-1.5 1.5M3 14h2M25 14h2"/>
      </svg>
    </div>
    <div class="brand"><i></i>Terravista NQ</div>
  </section>

  <!-- Oil & gas research -->
  <section class="slide col-l row5">
    <div class="photo" role="img" aria-label="Map of well locations and seismic study area" style="left:0;top:3px;width:91px;height:136px;background:linear-gradient(135deg,#e9eef0,#cfe3d2 45%,#e6d4de 75%,#d9e8ef)"></div>
    <div class="abs h g" style="left:108px;top:18px;font-size:13px;font-family:'PT Sans',sans-serif">OIL &amp; GAS</div>
    <div class="abs g" style="left:108px;top:31px;font-size:6.2px;font-weight:600">Innovative Energy Research as a Competitive Advantage</div>
    <div class="abs txt" style="left:108px;top:40px;width:230px;font-size:3.4px">
      <p class="g">The region's energy sector supports thousands of jobs and supplies domestic and global markets. According to the Continental Energy Producers Council, revenue and capital spending reached a new high in 2018 and gas output is expected to rise. Collecting, interpreting and sharing new data helps guide clean, responsible energy development and attract investment.</p>
      <div class="s" style="font-weight:700;font-size:5.6px;margin:2px 0">Facilitating Responsible Natural Resource Development</div>
      <p class="s">We have been funding research into induced seismicity in the northeast since 2012, especially near communities and infrastructure. The public research informs industry, government and community decisions and helps reduce the likelihood and impact of induced seismicity in the future. Many factors affect how fluid injection can trigger earthquakes, including local stress, fault orientation and injection rate.</p>
      <div class="s" style="font-size:4.6px">Northeast Focus</div>
      <p class="s">This research focuses on the Harlow Play, a gas-prone area within the Western Interior Basin that holds major natural gas deposits.</p>
      <p class="s">• Study of observed seismicity in the Harlow Play<br>• Review of shale gas extraction impacts<br>• Scientific review of hydraulic fracturing practice</p>
    </div>
    <div class="pageno" style="right:16px">9</div>
    <div class="brand"><i></i>Terravista NQ</div>
  </section>

  <!-- More space -->
  <section class="slide col-r row5">
    <div class="abs h g" style="left:43px;top:30px;font-size:13px;line-height:1.25;font-family:'PT Sans',sans-serif">More Space For<br>Expose<br>Work &amp; Develop</div>
    <div class="abs g" style="left:43px;top:86px;font-size:4.6px;font-weight:700">Oil &amp; Gas Subtitle</div>
    <div class="abs txt s" style="left:43px;top:97px;width:130px;font-size:3.6px;line-height:1.5">
      <p style="margin-bottom:5px">Our monitoring network tracks ground motion, water quality and air data near active sites. Readings are shared monthly so that communities and operators can follow trends and respond early. New sensors added this year extend coverage to remote valleys where little data existed before, and results feed into guidance for safe practice.</p>
      <p>Next steps include a public dashboard and a joint review with university partners later this year.</p>
    </div>
    <div class="photo" role="img" aria-label="Survey drone at sunset" style="left:236px;top:3px;width:90px;height:100px;background:linear-gradient(170deg,#d8a45a,#6a5a48 50%,#2a2622)"></div>
    <div class="photo" role="img" aria-label="Researcher collecting a water sample outdoors" style="left:236px;top:103px;width:90px;height:101px;background:linear-gradient(170deg,#c7d6dc,#7aa8c2 45%,#6e8a4e)"></div>
    <div class="pageno">10</div>
    <div class="brand"><i></i>Terravista NQ</div>
  </section>

</div>
</body>
</html>
```